Im open to ideas.. I was thinking on my business cards aswell as my logo. a place for my name. email. phone number and abn..

ive attched a file with my business logo. which i dont love the colours.. i was think a dark background with charcoal letters so something along those colour schumes but im open to ideas..

BRM Constructions

```html
<!DOCTYPE html>
<html lang="en">
<head>
<meta charset="utf-8">
<title>BRM Constructions — Business Cards</title>
<link rel="stylesheet" href="https://fonts.googleapis.com/css2?family=Archivo:wght@400;700&display=swap">
<style>
  :root {
    --backdrop: #8c8c8c;
    --card: #1f1f1f;
    --ink: #f2f2f2;
    --ink-muted: #cfcfcf;
  }
  * { margin: 0; padding: 0; box-sizing: border-box; }
  html, body {
    width: 1200px;
    height: 844px;
    overflow: hidden;
    background: var(--backdrop);
    font-family: "Archivo", Arial, sans-serif;
  }
  .card-set {
    position: absolute;
    top: 279px;
    left: 80px;
    display: flex;
    gap: 40px;
  }
  .card {
    width: 500px;
    height: 286px;
    background: var(--card);
    border-radius: 4px;
    color: var(--ink);
    position: relative;
  }
  .card--front {
    display: flex;
    align-items: center;
    justify-content: center;
  }
  .wordmark {
    font-weight: 700;
    font-size: 40px;
    letter-spacing: 2px;
    text-transform: uppercase;
    color: var(--ink);
  }
  .card--back .wordmark-small {
    position: absolute;
    left: 34px;
    top: 58px;
    font-weight: 700;
    font-size: 13px;
    letter-spacing: 1px;
    text-transform: uppercase;
    color: var(--ink);
  }
  .contact {
    position: absolute;
    left: 220px;
    top: 54px;
    line-height: 1.35;
  }
  .contact__name {
    font-weight: 700;
    font-size: 20px;
    letter-spacing: 1px;
    text-transform: uppercase;
  }
  .contact__role {
    font-size: 11px;
    letter-spacing: 1.5px;
    text-transform: uppercase;
    color: var(--ink-muted);
    margin-bottom: 6px;
  }
  .contact__line {
    font-size: 15px;
    color: var(--ink-muted);
  }
</style>
</head>
<body>
  <div class="card-set">
    <section class="card card--front">
      <span class="wordmark">BRM Constructions</span>
    </section>
    <section class="card card--back">
      <span class="wordmark-small">BRM Constructions</span>
      <div class="contact">
        <p class="contact__name">Daniel Reyes</p>
        <p class="contact__role">Construction Manager</p>
        <p class="contact__line">(555) 210-4786</p>
        <p class="contact__line">dreyes@brmconstructions.com</p>
        <p class="contact__line">ABN 9876543210</p>
      </div>
    </section>
  </div>
</body>
</html>
```